Redesign two existing website pages and one new landing page for dental office

I need to redesign two webpages on my dental website, the Home page (http://velbridgedental.com) and the Dental Implant Services page (http://www.velbridgedental.com/dental-implant-services) and also create a landing page for the Dental Implant Services page.

Please use the same color scheme, slogans and subtitles for the redesign pages and create a reserved video spot on each page. The video spots should not be too big but not too small either and positioned in a central key location on each of the pages. The final redesigned pages should communicate leadership, confidence and trust.

The new landing page for the Dental implant Services page must not have any hyperlinks on the page and must entice the viewer to give name and email before downloading a "Free" eBook called "Is a Fuller Smile Worth the Wait?" Any added photo images to this new page must be smiling.
Updates

Project Deadline Extended Reason: I got feedback that my project was not long enough so I'm extending it by 5 days. Added Thursday, April 16, 2015

Target Market(s)

People who are middle-age to seniors.

Industry/Entity Type

Dental

Coding

Coded - Design and coding required

Number of Pages Required

3 page

Requirements
Must have
• Compatible with existing website colors and theme.

```html
<!DOCTYPE html>
<html lang="en">
<head>
<meta charset="utf-8">
<title>Velbridge Dental Care</title>
<link href="https://fonts.googleapis.com/css2?family=Raleway:wght@400;500;600&family=Open+Sans:wght@400;600&display=swap" rel="stylesheet">
<style>
:root{
  --green:#23362f;
  --green-2:#1d2b26;
  --orange:#c5570f;
  --orange-band:#c95b12;
  --teal:#7f9d97;
  --light:#eef2f1;
  --text:#5c5c5c;
  --head:#2b3a35;
  --rule:#dcdcdc;
}
*{box-sizing:border-box;margin:0;padding:0}
html,body{width:1200px;height:2184px;overflow:hidden}
body{font-family:"Open Sans",Arial,sans-serif;color:var(--text);background:#fff;position:relative}
.abs{position:absolute}
.wrap{position:absolute;left:111px;width:978px}
h1,h2,h3,h4{font-family:"Raleway",Arial,sans-serif;font-weight:500;color:var(--head)}

/* header */
.brand{left:111px;top:38px;display:flex;align-items:center;gap:10px}
.brand-dot{width:14px;height:14px;border-radius:50%;background:var(--teal)}
.brand-name{font-family:"Raleway",sans-serif;font-size:34px;color:#4f7a72;font-weight:500}
.call{right:111px;top:36px;display:flex;gap:14px;align-items:center}
.call small{display:block;font-family:"Raleway",sans-serif;font-size:16px;color:#555;letter-spacing:.5px}
.call strong{display:block;font-family:"Raleway",sans-serif;font-size:27px;font-weight:500;color:#333;line-height:1}

/* nav */
.nav{top:112px;height:58px;background:var(--green);display:flex;align-items:center;padding:0 20px;z-index:2}
.nav a{font-family:"Raleway",sans-serif;font-size:12.5px;color:#fff;text-decoration:none;margin-right:40px;letter-spacing:.3px;white-space:nowrap}
.nav a.active{background:var(--orange);border-radius:18px;padding:10px 20px}
.social{margin-left:auto;display:flex;gap:7px}
.social span{width:26px;height:26px;border-radius:50%;background:#5f8a9b}
.social span:nth-child(5){background:#c94b2a}

/* hero */
.hero-band{left:0;top:170px;width:1200px;height:541px;background:var(--teal)}
.hero{top:170px;height:541px;background:linear-gradient(100deg,#e9eceb 0%,#dfe3e2 40%,#c4b8a8 65%,#d9dad5 100%)}
.hero-title{position:absolute;left:83px;top:296px;font-family:"Raleway",sans-serif;font-size:31px;font-weight:500;color:var(--head);line-height:38px;letter-spacing:.3px;white-space:nowrap}
.hero-title em{font-style:normal;color:var(--orange)}
.dots{position:absolute;left:459px;top:508px;display:flex;gap:7px}
.dots i{width:8px;height:8px;border-radius:50%;background:#2c3a36}
.dots i.on{background:var(--orange)}
.hero-shadow{left:130px;top:708px;width:940px;height:22px;border-radius:50%;background:radial-gradient(ellipse at center,rgba(0,0,0,.45),rgba(0,0,0,0) 70%)}

/* features */
.features{top:764px;display:flex;justify-content:space-between}
.feature{display:flex;gap:16px;width:318px}
.feature .ic{flex:none;width:80px;height:80px;border-radius:50%;background:var(--green);display:flex;align-items:center;justify-content:center}
.feature h3{font-size:14.5px;margin-top:12px;color:#2b3a35;white-space:nowrap}
.feature p{font-size:11.5px;line-height:20px;color:#777;margin-top:3px}

/* service cards */
.services-bg{left:0;top:887px;width:1200px;height:359px;background:var(--light)}
.card{position:absolute;top:887px;width:477px;height:359px;border:1px solid #cfd6d4;background:linear-gradient(90deg,#f2f4f3,#e9eeec)}
.card .photo{position:absolute;right:0;top:0;width:175px;height:230px;background:linear-gradient(180deg,#e7ecec,#cfd9dc)}
.card h2{position:absolute;left:25px;top:30px;font-size:22px;white-space:nowrap}
.card .sub{position:absolute;left:25px;top:68px;font-size:11.5px;color:var(--orange);text-transform:uppercase;white-space:nowrap}
.card p{position:absolute;left:25px;top:90px;width:285px;font-size:11.5px;line-height:24px;color:#6a6a6a}
.btn{position:absolute;left:25px;top:170px;background:var(--orange);color:#fff;font-size:12px;padding:10px 17px;font-family:"Raleway",sans-serif}
.card .remember{position:absolute;left:0;top:230px;width:100%;height:129px;background:var(--green);padding:10px 25px;color:#c5d0cc}
.remember h4{color:#fff;font-size:13px;font-weight:600;margin-bottom:4px}
.remember li{list-style:none;font-size:10.5px;line-height:16px;margin-bottom:7px;padding-left:13px;position:relative}
.remember li:before{content:"";position:absolute;left:0;top:4px;width:6px;height:6px;border:1.5px solid var(--orange);border-radius:50%}

/* lists */
.lists{top:1276px;display:flex;justify-content:space-between}
.col{width:226px}
.col h3{font-size:15.5px;color:#2b3a35;margin-bottom:12px;white-space:nowrap}
.col li{list-style:none;font-size:10.5px;color:#666;height:34px;line-height:34px;border-bottom:1px solid var(--rule);padding-left:12px;position:relative;white-space:nowrap}
.col li:last-child{border:0}
.col li:before{content:"➔";position:absolute;left:0;color:var(--orange);font-size:10px}

/* intro */
.intro-title{top:1443px;width:1200px;text-align:center;font-size:26px;font-family:"Raleway",sans-serif;font-weight:500;color:#2b3a35}
.intro-video{left:111px;top:1493px;width:308px;height:182px;background:linear-gradient(90deg,#b9d4ea 0%,#d9e8f2 40%,#e9b3a6 60%,#f1d4c8 100%);border:4px solid #fff;box-shadow:0 3px 8px rgba(0,0,0,.25);display:flex;align-items:center;justify-content:center}
.play{width:54px;height:54px;border-radius:50%;background:rgba(35,54,47,.85);display:flex;align-items:center;justify-content:center}
.intro-text{left:444px;top:1498px;width:646px}
.intro-text h3{font-size:15px;color:var(--orange);font-weight:600}
.intro-text .lead{font-size:13px;color:#444;margin:7px 0 2px}
.intro-text .lead b{color:var(--orange);font-weight:400}
.intro-text p{font-size:11.5px;line-height:26px;color:#6a6a6a}

/* cta band */
.cta{left:0;top:1712px;width:1200px;height:184px;background:var(--orange-band);text-align:center;color:#fff}
.cta h2{color:#fff;font-size:21px;font-weight:500;margin-top:38px}
.cta p{font-size:15px;margin-top:6px;color:#fde3d0}
.cta .sched{display:inline-flex;gap:7px;align-items:center;margin-top:18px;background:var(--green);padding:15px 37px;font-family:"Raleway",sans-serif;font-size:15px;font-weight:600}

/* footer */
.footer{left:0;top:1896px;width:1200px;height:222px;background:var(--green-2)}
.fcol{position:absolute;top:34px;color:#9aa6a2;font-size:11px}
.fcol h4{color:#fff;font-size:15px;font-weight:500;margin-bottom:16px}
.post{display:flex;gap:12px;margin-bottom:14px}
.post .th{flex:none;width:68px;height:52px;background:linear-gradient(135deg,#d7e1e6,#8fa7b4);border:2px solid #fff}
.post b{display:block;color:#fff;font-weight:400;font-size:12px;margin-bottom:3px}
.post span{line-height:16px;display:block;width:160px}
.links{display:grid;grid-template-columns:112px 110px;row-gap:10px}
.contact{width:230px}
.contact div{display:flex;gap:12px;margin-bottom:12px;line-height:18px}
.contact div span{width:205px}
.contact b{color:#fff;font-weight:400}
.map{width:204px;height:125px;background:linear-gradient(135deg,#eef0ea,#dfe3d8);border:3px solid #fff}
.bottom{left:0;top:2118px;width:1200px;height:66px;background:#1a1f1d;text-align:center;line-height:66px;font-size:11px;color:#7d8784}
</style>
</head>
<body>

<header>
  <div class="abs brand"><span class="brand-dot"></span><span class="brand-name">Velbridge Dental Care</span></div>
  <div class="abs call">
    <svg width="32" height="32" viewBox="0 0 24 24"><path fill="#c5570f" d="M6.6 10.8a15.1 15.1 0 0 0 6.6 6.6l2.2-2.2c.3-.3.7-.4 1-.2 1.1.4 2.3.6 3.6.6.6 0 1 .4 1 1V20c0 .6-.4 1-1 1A17 17 0 0 1 3 4c0-.6.4-1 1-1h3.5c.6 0 1 .4 1 1 0 1.3.2 2.5.6 3.6.1.3 0 .7-.2 1z"/></svg>
    <div><small>CALL US TODAY!</small><strong>(555) 014-2870</strong></div>
  </div>
</header>

<nav class="wrap nav">
  <a class="active">HOME</a><a>ABOUT US</a><a>DENTAL SERVICES</a><a>BLOG</a><a>CONTACT US</a><a>TESTIMONIALS</a>
  <div class="social" aria-label="Social links"><span></span><span></span><span></span><span></span><span></span></div>
</nav>

<div class="abs hero-band"></div>
<section class="wrap hero" role="img" aria-label="Smiling man relaxing in a dental chair">
  <h1 class="hero-title">LIFE-CHANGING <em>FAMILY</em><br><em>DENTAL CARE</em> IN SUGAR LAND</h1>
  <div class="dots"><i></i><i class="on"></i><i></i><i></i></div>
</section>
<div class="abs hero-shadow"></div>

<section class="wrap features">
  <div class="feature">
    <div class="ic"><svg width="22" height="32" viewBox="0 0 22 32"><rect x="2" y="1" width="18" height="30" rx="3" fill="none" stroke="#fff" stroke-width="2"/><circle cx="11" cy="26" r="1.6" fill="#fff"/></svg></div>
    <div><h3>GET DR. VELBRIDGE'S APP</h3><p>Lorem ipsum dolor sit amet, consec tetuer adipiscing elit.</p></div>
  </div>
  <div class="feature">
    <div class="ic"><svg width="30" height="30" viewBox="0 0 30 30"><rect x="2" y="5" width="26" height="23" fill="none" stroke="#fff" stroke-width="2"/><path d="M2 11h26M9 2v6M21 2v6" stroke="#fff" stroke-width="2"/><path d="M7 15h4v3H7zm6 0h4v3h-4zm6 0h4v3h-4zM7 21h4v3H7zm6 0h4v3h-4zm6 0h4v3h-4z" fill="#fff"/></svg></div>
    <div><h3>REQUEST AN APPOINTMENT</h3><p>Eodem modo typi, qui nunc nobis videntur parum clari, fiant sollemnes</p></div>
  </div>
  <div class="feature">
    <div class="ic"><svg width="24" height="30" viewBox="0 0 24 30"><path d="M2 1h14l6 6v22H2z" fill="none" stroke="#fff" stroke-width="2"/><path d="M6 12h12M6 17h12M6 22h12" stroke="#fff" stroke-width="2"/></svg></div>
    <div><h3>NEW PATIENT ONLINE FORMS</h3><p>Ut wisi enim ad minim veniam, quis nostrud exerci tation ullamcorper</p></div>
  </div>
</section>

<div class="abs services-bg"></div>
<article class="card" style="left:111px">
  <div class="photo" role="img" aria-label="Smiling dentist and hygienist"></div>
  <h2>DENTAL HYGIENE SERVICES</h2>
  <div class="sub">Achieve better health with prevention</div>
  <p>Maintain healthy teeth and gums with consistent dental exams and teeth cleanings by one of our professional dental hygienists.</p>
  <span class="btn">LEARN MORE</span>
  <div class="remember"><h4>REMEMBER :</h4><ul>
    <li>Improve your health with consistent dental checkups</li>
    <li>Save time with convenient appointment options close to home</li>
    <li>Teach kids to develop good dental habits and to maintain a life time of preventive dental care</li></ul></div>
</article>
<article class="card" style="left:612px">
  <div class="photo" role="img" aria-label="Patient receiving a dental examination"></div>
  <h2>DENTAL EMERGENCY SERVICES</h2>
  <div class="sub">Stop pain from tooth trauma and infection</div>
  <p>Dental emergencies can and will happen suddenly. Treat all tooth infections and dental trauma (without delay) whenever they occur.</p>
  <span class="btn">LEARN MORE</span>
  <div class="remember"><h4>REMEMBER :</h4><ul>
    <li>Repair your broken, fractured, or lost teeth</li>
    <li>Call our dental office to reach our Sugar Land dentist for an immediate response to avoid further tooth damage and infection</li>
    <li>Overcome dental anxiety with comforting dental sedation</li></ul></div>
</article>

<section class="wrap lists">
  <div class="col"><h3>BEAUTIFUL DENTURES</h3><ul><li>What is a Denture?</li><li>Who Needs a Denture?</li><li>Just How Are Dentures Made?</li></ul></div>
  <div class="col"><h3>COSMETIC DENTISTRY</h3><ul><li>Whiten Your Teeth</li><li>Porcelain Veneers</li><li>Clear Aligner Therapy Orthodontics</li></ul></div>
  <div class="col"><h3>DENTAL IMPLANT SERVICES</h3><ul><li>Anchorage to the jaw bone</li><li>Replaces 1 or more missing teeth</li><li>Stabilizes loose, floppy dentures</li></ul></div>
  <div class="col"><h3>SEDATION DENTISTRY</h3><ul><li>Control Dental Fear with Sedation Dentistry</li><li>Dental Pain Management</li><li>Relaxed and Tranquil Treatment</li></ul></div>
</section>

<h2 class="abs intro-title">DON'T WAIT 'TIL IT HURTS!</h2>
<div class="abs intro-video" role="img" aria-label="Video spot: bright smile beside blue flowers">
  <span class="play"><svg width="20" height="22" viewBox="0 0 20 22"><path d="M3 1l16 10L3 21z" fill="#fff"/></svg></span>
</div>
<section class="abs intro-text">
  <h3>GET ACQUANTED TODAY WITH COMFORTABLE DENTAL CARE.</h3>
  <div class="lead"><b>Request an Appointment!</b> We will contact you right away to schedule your dental appointment.</div>
  <p>Lorem ipsum dolor sit amet, consectetuer adipiscing elit, sed diam nonummy nibh euismod tincidunt ut laoreet dolore magna aliquam erat volutpat. Ut wisi enim ad minim veniam, quis nostrud exerci tation ullamcorper suscipit lobortis nisl ut aliquip ex ea commodo consequat.</p>
  <p>Mirum est notare quam littera gothica, quam nunc putamus parum claram, anteposuerit litterarum formas humanitatis per seacula quarta decima et quinta decima. Eodem modo typi.</p>
</section>

<section class="abs cta">
  <h2>COMPREHENSIVE FAMILY DENTISTRY IN ONE SUGAR LAND DENTAL OFFICE!</h2>
  <p>Don't Wait 'til it Hurts! Schedule Your Dental Appointment Today</p>
  <span class="sched"><svg width="15" height="15" viewBox="0 0 30 30"><rect x="2" y="5" width="26" height="23" fill="none" stroke="#fff" stroke-width="3"/><path d="M2 11h26M9 2v6M21 2v6" stroke="#fff" stroke-width="3"/></svg>SCHEDULE AN APPOINTMENT</span>
</section>

<footer class="abs footer">
  <div class="fcol" style="left:111px"><h4>RECENT BLOG POSTS</h4>
    <div class="post"><div class="th" role="img" aria-label="Dentist with patient"></div><div><b>Lorem ipsum dolor sit</b><span>Ut wisi enim ad minim veniam, quis nostrud...</span></div></div>
    <div class="post"><div class="th" role="img" aria-label="Dental team"></div><div><b>Claritas est etiam process</b><span>Mirum est notare quam littera gothica, quam nunc</span></div></div>
  </div>
  <div class="fcol" style="left:374px"><h4>QUICK LINKS</h4>
    <div class="links"><span>Home</span><span>Testimonials</span><span>About Us</span><span>Privacy Policy</span><span>Our Service</span><span>Sitemap</span><span>Our Blog</span><span>Terms &amp; Conditions</span><span>Contact Us</span></div>
  </div>
  <div class="fcol contact" style="left:626px"><h4>CONTACT US</h4>
    <div><svg width="11" height="15" viewBox="0 0 12 16"><path fill="#c5570f" d="M6 0a6 6 0 0 0-6 6c0 4.5 6 10 6 10s6-5.5 6-10a6 6 0 0 0-6-6zm0 8.5A2.5 2.5 0 1 1 6 3.5a2.5 2.5 0 0 1 0 5z"/></svg><span><b>VELBRIDGE DENTAL CARE</b><br>Harborview Medical Center, 2400 Ridge Rd, Ste. #120, Sugar Land, TX 77478</span></div>
    <div><svg width="13" height="11" viewBox="0 0 14 11"><rect width="14" height="11" fill="#c5570f"/><path d="M0 0l7 6 7-6" fill="none" stroke="#1d2b26" stroke-width="1.2"/></svg><span>info@velbridgedental.com</span></div>
    <div><svg width="13" height="13" viewBox="0 0 14 14"><rect width="14" height="14" rx="2" fill="#c5570f"/><path d="M4 3l2 2-1 1a6 6 0 0 0 3 3l1-1 2 2-1 1.5C6 11 3 8 2.5 4.5z" fill="#1d2b26"/></svg><span>(555) 014-2870</span></div>
  </div>
  <div class="fcol" style="left:876px"><h4>OUR LOCATION</h4>
    <div class="map" role="img" aria-label="Street map of the office location"></div>
  </div>
</footer>
<div class="abs bottom">Copyrights @ 2015 Velbridge Dental Care. All Right Reserved.</div>

</body>
</html>
```